KLV Plant Services

We are a heavy diesel mechanical business with additional air con certificates, remapping engine rebuilt

Contact Information for Business Card

Company Name, Director Name, Managing Director, Contact details, email and website

Font styles to use
Serif
Script

```html
<!DOCTYPE html>
<html lang="en">
<head>
<meta charset="utf-8">
<title>KLV Plant Services – Business Card</title>
<link href="https://fonts.googleapis.com/css2?family=Libre+Baskerville:wght@400;700&family=Dancing+Script:wght@700&display=swap" rel="stylesheet">
<style>
  :root {
    --navy: #06065c;
    --paper: #f7f7f7;
    --ink: #2b2b2b;
    --grey-text: #6a6a6a;
    --backdrop: #9a9a9a;
    --white: #ffffff;
  }
  * { margin: 0; padding: 0; box-sizing: border-box; }
  html, body {
    width: 1200px;
    height: 1050px;
    overflow: hidden;
    background: var(--backdrop);
    font-family: "Libre Baskerville", Georgia, serif;
  }
  .canvas {
    position: relative;
    width: 1200px;
    height: 1050px;
  }
  .card {
    position: absolute;
    border-radius: 22px;
    box-shadow: 0 6px 18px rgba(0,0,0,0.25);
  }
  .card-front {
    left: 90px;
    top: 225px;
    width: 350px;
    height: 600px;
    background: var(--paper);
    border: 3px solid var(--navy);
  }
  .front-brand {
    position: absolute;
    top: 34px;
    right: 30px;
    display: flex;
    align-items: center;
    gap: 8px;
    color: var(--navy);
    font-weight: 700;
    font-size: 14px;
  }
  .front-brand .brand-dot {
    width: 12px;
    height: 12px;
    border-radius: 50%;
    background: var(--navy);
    flex: none;
  }
  .contact-block {
    position: absolute;
    left: 34px;
    right: 24px;
    bottom: 40px;
    color: var(--ink);
  }
  .person-name {
    font-family: "Dancing Script", "Brush Script MT", cursive;
    color: var(--navy);
    font-weight: 700;
    font-size: 32px;
    line-height: 1.1;
  }
  .person-role {
    color: var(--grey-text);
    font-size: 14px;
    margin-top: 4px;
  }
  .rule {
    width: 32px;
    height: 1px;
    background: var(--ink);
    margin: 16px 0;
  }
  .address, .details {
    font-size: 13px;
    line-height: 1.6;
  }
  .details .label {
    color: var(--navy);
    font-weight: 700;
    display: inline-block;
    width: 28px;
  }
  .card-back {
    left: 510px;
    top: 350px;
    width: 600px;
    height: 350px;
    background: var(--navy);
    border: 3px solid var(--white);
    display: flex;
    align-items: center;
    justify-content: center;
  }
  .back-brand {
    display: flex;
    align-items: center;
    gap: 18px;
    color: var(--white);
    font-weight: 700;
  }
  .back-brand .brand-ring {
    width: 52px;
    height: 52px;
    border-radius: 50%;
    border: 4px solid var(--white);
    flex: none;
  }
  .back-brand .brand-name {
    font-size: 36px;
    line-height: 1;
    white-space: nowrap;
  }
</style>
</head>
<body>
<main class="canvas">
  <section class="card card-front">
    <div class="front-brand">
      <span class="brand-dot"></span>
      <span class="brand-name">KLV Plant Services</span>
    </div>
    <div class="contact-block">
      <p class="person-name">Owen Hartley</p>
      <p class="person-role">Managing Director</p>
      <div class="rule"></div>
      <p class="address">2719 Alder Crest Road<br>Milbrook, NY 12545</p>
      <div class="rule"></div>
      <p class="details"><span class="label">P :</span>(512) 6290-4418</p>
      <p class="details"><span class="label">E :</span>name@klvplant.com</p>
      <p class="details"><span class="label">W :</span>www.klvplant.com</p>
    </div>
  </section>
  <section class="card card-back">
    <div class="back-brand">
      <span class="brand-ring"></span>
      <span class="brand-name">KLV Plant Services</span>
    </div>
  </section>
</main>
</body>
</html>
```